NZ First of it's kind solutions directory and marketplace for busy Mums needs a business card design

We need a business card design for our new nationwide business in NZ (long term plans to go global). We provide solutions to the everyday challenges that busy Mums face by connecting them with quality communities and suppliers of carefully selected, relevant products and services. We sell direct via our online marketplace. The final design should communicate our values of inclusivity, quality and smart solutions. Colours should incorporate our logo colour palette of #477077 and #6ba8b2. Our website is at https://www.brightnestmums.example

Target Market(s)

busy Mums, Age 28 – 50, female, income over $100K, location main centres NZ primarily but NZ wide. Is likely juggling work or career with a young family. Probably had hobbies which have fallen by the wayside.
-Wants to succeed in her chosen career without compromising on family life
-to successfully juggle her career without feeling like she is compromising her children
- Is time poor, something always has to give and it’s generally her health (she’ll stay up late, get stressed)
- probably ex corporate or professional career. Has discretional income

Industry/Entity Type

Business

Contact Information for Business Card

Lena Forbisher, Founder, BrightNestMums.example (Strapline Tap; Gather; Sorted), 47 Kowhai Terrace, Ellerslie, Auckland 1051, New Zealand. Mob: 021 483 517 Ph: +64 (0)9 571 4860

Font styles to use
Other font styles liked:
• Raleway, and/or Architects Daughter

Colors
00a990
33b8a4
86cfc6
cfeae6

Requirements
Must have
• the above details, streamline. the logo and colours associated with those logos
Should not have
• foil or metallic colours

```html
<!DOCTYPE html>
<html lang="en">
<head>
<meta charset="utf-8">
<title>BrightNestMums business card</title>
<link rel="stylesheet" href="https://fonts.googleapis.com/css2?family=Nunito:wght@800&family=Roboto+Condensed:ital,wght@0,400;1,400&display=swap">
<style>
  :root {
    --brand-dark: #3a5c65;
    --brand-teal: #5b9aa5;
    --card-white: #f7f7f7;
    --backdrop: #e4e4e4;
    --ink-light: #ffffff;
  }
  * { box-sizing: border-box; margin: 0; padding: 0; }
  html, body { width: 1200px; height: 576px; overflow: hidden; }
  body { background: var(--backdrop); position: relative; font-family: "Roboto Condensed", sans-serif; }

  .card {
    position: absolute;
    top: 138px;
    background: var(--card-white);
    border-radius: 14px;
    overflow: hidden;
    box-shadow: 0 3px 6px rgba(0,0,0,0.18);
  }
  .card--front { left: 82px; width: 484px; height: 294px; }
  .card--back { left: 602px; width: 481px; height: 290px; }

  .wordmark {
    font-family: "Nunito", sans-serif;
    font-weight: 800;
    color: var(--brand-dark);
    letter-spacing: -0.5px;
    white-space: nowrap;
    line-height: 1;
  }
  .brand-dot {
    display: inline-block;
    border-radius: 50%;
    background: var(--brand-dark);
  }

  /* Front */
  .front-brand { position: absolute; left: 34px; top: 120px; display: flex; align-items: center; gap: 10px; }
  .front-brand .brand-dot { width: 30px; height: 30px; }
  .front-brand .wordmark { font-size: 24px; }
  .strapline {
    position: absolute; left: 76px; top: 164px;
    font-size: 9px; letter-spacing: 3px; color: var(--brand-dark); text-transform: uppercase;
  }
  .strapline .divider { color: var(--brand-teal); margin: 0 3px; }
  .front-motif {
    position: absolute; left: 282px; top: 106px;
    width: 200px; height: 200px; border-radius: 50%;
    background: var(--brand-dark);
  }

  /* Back */
  .back-brand { position: absolute; left: 30px; top: 46px; display: flex; align-items: center; gap: 12px; }
  .back-brand .brand-dot { width: 38px; height: 38px; }
  .back-brand .wordmark { font-size: 32px; }
  .holder { position: absolute; left: 36px; top: 138px; }
  .holder__name { font-family: "Nunito", sans-serif; font-weight: 800; font-size: 20px; color: var(--brand-dark); }
  .holder__role { font-style: italic; font-size: 12px; color: var(--brand-dark); margin-top: 1px; }
  .wave { position: absolute; left: 0; top: 0; }
  .contact-list {
    position: absolute; right: 20px; top: 186px; list-style: none;
    color: var(--ink-light); font-size: 12.5px; text-align: right;
  }
  .contact-list li { height: 18.4px; display: flex; justify-content: flex-end; align-items: center; gap: 9px; }
  .contact-list svg { width: 11px; height: 11px; fill: var(--ink-light); flex: none; }
</style>
</head>
<body>

<section class="card card--front" aria-label="Card front">
  <div class="front-brand">
    <span class="brand-dot"></span>
    <span class="wordmark">BrightNestMums</span>
  </div>
  <p class="strapline">Tap<span class="divider">|</span>Gather<span class="divider">|</span>Sorted</p>
  <div class="front-motif" role="img" aria-label="Large shopping bag motif in brand colours"></div>
</section>

<section class="card card--back" aria-label="Card back">
  <div class="back-brand">
    <span class="brand-dot"></span>
    <span class="wordmark">BrightNestMums</span>
  </div>

  <svg class="wave" width="481" height="290" viewBox="0 0 481 290" aria-hidden="true">
    <path d="M0 196 C90 240 210 214 310 168 S430 118 481 124 L481 134 C430 130 360 150 310 178 S110 244 0 212 Z" fill="var(--brand-teal)"/>
    <path d="M0 234 C110 282 230 240 320 196 S440 148 481 152 L481 290 L0 290 Z" fill="var(--brand-dark)"/>
    <path d="M40 222 C140 250 220 236 300 206" stroke="var(--card-white)" stroke-width="3" fill="none"/>
  </svg>

  <div class="holder">
    <p class="holder__name">Lena Forbisher</p>
    <p class="holder__role">Founder</p>
  </div>

  <ul class="contact-list">
    <li>021 483 517
      <svg viewBox="0 0 12 12"><rect x="3" y="0.5" width="6" height="11" rx="1.2"/><rect x="4" y="2" width="4" height="6.5" fill="var(--brand-dark)"/></svg></li>
    <li>+64 (0)9 571 4860
      <svg viewBox="0 0 12 12"><path d="M1 4 C1 2 3 1.5 6 1.5 S11 2 11 4 L9 5 L8 3.5 H4 L3 5 Z"/><rect x="2.5" y="6" width="7" height="5" rx="1"/></svg></li>
    <li>www.BrightNestMums.example
      <svg viewBox="0 0 12 12"><rect x="0.5" y="2" width="11" height="8" rx="1"/><path d="M1 2.5 L6 6.5 L11 2.5" stroke="var(--brand-dark)" fill="none"/></svg></li>
    <li>lena@brightnestmums.example
      <svg viewBox="0 0 12 12"><circle cx="6" cy="6" r="5.2" fill="none" stroke="#fff" stroke-width="1.2"/><ellipse cx="6" cy="6" rx="2.2" ry="5.2" fill="none" stroke="#fff"/><path d="M1 6 H11" stroke="#fff"/></svg></li>
    <li>47 Kowhai Terrace, Ellerslie, Auckland 1051, New Zealand
      <svg viewBox="0 0 12 12"><path d="M6 11.5 L2.2 6 A4.2 4.2 0 1 1 9.8 6 Z"/><circle cx="6" cy="4.3" r="1.5" fill="var(--brand-dark)"/></svg></li>
  </ul>
</section>

</body>
</html>
```